Business Card Design

We are a commercial real estate brokerage in San Francisco, leasing office buildings downtown.
I would like a clean, elegant look. Simple but powerful .

Industry/Entity Type

Business

Contact Information for Business Card

Derek Holloway
lic# 07258143
415.555.0172
derek@velt-commercial.example
velt-commercial.example

```html
<!DOCTYPE html>
<html lang="en">
<head>
<meta charset="utf-8">
<title>Velt Commercial — Business Card</title>
<link rel="stylesheet" href="https://fonts.googleapis.com/css2?family=Arimo:ital,wght@0,400;0,700;1,400&display=swap">
<style>
  :root {
    --page-bg: #d9d6d2;
    --card-bg: #f1f2f3;
    --card-haze: #f3dde0;
    --brand: #3d4f6e;
    --name: #56698c;
    --text: #4a4a4a;
    --icon: #5b5b5b;
    --city-dark: #1f1f22;
    --city-mid: #4a4a50;
    --band-top: #3a3636;
    --band-bottom: #1c1a1a;
    --tagline: #d9b6bd;
  }
  html, body {
    margin: 0;
    width: 1200px;
    height: 969px;
    overflow: hidden;
    background: var(--page-bg);
    font-family: "Arimo", Arial, sans-serif;
  }
  .card {
    position: absolute;
    left: 100px;
    top: 200px;
    width: 1000px;
    height: 568px;
    background:
      radial-gradient(ellipse 420px 160px at 300px 470px, var(--card-haze), transparent 70%),
      linear-gradient(180deg, #f7f8f9 0%, var(--card-bg) 100%);
    box-shadow: 0 10px 30px rgba(0,0,0,0.18);
    overflow: hidden;
  }
  .brand {
    position: absolute;
    left: 55px;
    top: 88px;
    display: flex;
    align-items: center;
    gap: 16px;
  }
  .brand-mark {
    width: 34px;
    height: 34px;
    background: var(--brand);
  }
  .brand-name {
    font-weight: 700;
    font-size: 38px;
    letter-spacing: 1px;
    color: var(--brand);
  }
  .agent-name {
    position: absolute;
    left: 55px;
    top: 228px;
    margin: 0;
    font-size: 34px;
    font-weight: 700;
    color: var(--name);
  }
  .license {
    position: absolute;
    left: 55px;
    top: 286px;
    margin: 0;
    font-size: 26px;
    color: var(--text);
  }
  .contact-list {
    position: absolute;
    left: 55px;
    top: 327px;
    margin: 0;
    padding: 0;
    list-style: none;
    font-size: 25px;
    color: var(--text);
  }
  .contact-list li {
    display: flex;
    align-items: center;
    gap: 12px;
    height: 39px;
  }
  .contact-icon {
    width: 24px;
    height: 24px;
    fill: var(--icon);
    flex: none;
  }
  .skyline {
    position: absolute;
    left: 491px;
    top: 5px;
    width: 509px;
    height: 465px;
    background: linear-gradient(160deg, var(--city-mid) 0%, var(--city-dark) 70%);
    clip-path: polygon(8% 0, 100% 0, 100% 100%, 0 100%, 0 82%, 8% 82%);
  }
  .band {
    position: absolute;
    left: 0;
    bottom: 0;
    width: 100%;
    height: 98px;
    background: linear-gradient(180deg, var(--band-top), var(--band-bottom));
    display: flex;
    flex-direction: column;
    align-items: center;
    justify-content: center;
  }
  .tagline {
    margin: 0;
    font-style: italic;
    font-size: 24px;
    line-height: 34px;
    color: var(--tagline);
    text-align: center;
  }
</style>
</head>
<body>
  <div class="card">
    <div class="brand">
      <div class="brand-mark"></div>
      <div class="brand-name">VELT COMMERCIAL</div>
    </div>

    <h1 class="agent-name">Derek Holloway</h1>
    <p class="license">lic# 07258143</p>

    <ul class="contact-list">
      <li>
        <svg class="contact-icon" viewBox="0 0 24 24" aria-hidden="true"><path d="M6.6 10.8c1.4 2.8 3.8 5.1 6.6 6.6l2.2-2.2c.3-.3.7-.4 1-.2 1.1.4 2.3.6 3.6.6.6 0 1 .4 1 1V20c0 .6-.4 1-1 1C10.6 21 3 13.4 3 4c0-.6.4-1 1-1h3.5c.6 0 1 .4 1 1 0 1.3.2 2.5.6 3.6.1.3 0 .7-.2 1z"/></svg>
        <span>415.555.0172</span>
      </li>
      <li>
        <svg class="contact-icon" viewBox="0 0 24 24" aria-hidden="true"><path d="M3 5h18v14H3z" /><path d="M3 5l9 7 9-7" fill="none" stroke="#f1f2f3" stroke-width="1.6"/></svg>
        <span>derek@velt-commercial.example</span>
      </li>
      <li>
        <svg class="contact-icon" viewBox="0 0 24 24" aria-hidden="true"><circle cx="12" cy="12" r="10"/><path d="M2 12h20M12 2c3 3 3 17 0 20M12 2c-3 3-3 17 0 20" fill="none" stroke="#f1f2f3" stroke-width="1.4"/></svg>
        <span>velt-commercial.example</span>
      </li>
    </ul>

    <div class="skyline" role="img" aria-label="Illustration of dark downtown office towers rising above an arched base"></div>

    <div class="band">
      <p class="tagline">commercial real estate brokerage in San Francisco<br>leasing office buildings downtown.</p>
    </div>
  </div>
</body>
</html>
```